Im open to ideas.. I was thinking on my business cards aswell as my logo. a place for my name. email. phone number and abn..

ive attched a file with my business logo. which i dont love the colours.. i was think a dark background with charcoal letters so something along those colour schumes but im open to ideas..

BRM Constructions

```html
<!DOCTYPE html>
<html lang="en">
<head>
<meta charset="utf-8">
<title>BRM Constructions – Business Card</title>
<link href="https://fonts.googleapis.com/css2?family=Open+Sans:wght@400;600;700&display=swap" rel="stylesheet">
<style>
  :root {
    --page-bg: #e9e7e4;
    --brand-red: #d9121b;
    --brand-red-dark: #a50d13;
    --charcoal: #2b2b2d;
    --charcoal-soft: #4a4a4d;
    --card-white: #ffffff;
    --text-grey: #555558;
  }
  * { box-sizing: border-box; margin: 0; padding: 0; }
  html, body {
    width: 1200px; height: 950px; overflow: hidden;
    background: var(--page-bg);
    font-family: "Open Sans", Arial, sans-serif;
  }
  .sheet {
    width: 1200px; height: 950px;
    display: flex; flex-direction: column;
    align-items: center; justify-content: center; gap: 50px;
  }
  .card {
    position: relative;
    width: 700px; height: 400px;
    overflow: hidden;
    box-shadow: 0 8px 24px rgba(0,0,0,0.18);
  }

  /* Back side */
  .card--back {
    background: linear-gradient(120deg, var(--brand-red) 0%, #c50f17 60%, var(--brand-red-dark) 100%);
    display: flex; flex-direction: column; align-items: center; justify-content: center;
    color: var(--card-white);
  }
  .card--back .wordmark { color: var(--card-white); font-size: 54px; }
  .card--back .website {
    margin-top: 14px; font-size: 20px; letter-spacing: 3px; font-weight: 400;
  }

  .wordmark {
    font-family: "Open Sans", Arial, sans-serif;
    font-weight: 700;
    letter-spacing: 1px;
    line-height: 1;
    white-space: nowrap;
  }

  /* Front side */
  .card--front { background: var(--card-white); }
  .card--front .wordmark {
    position: absolute; right: 48px; top: 120px;
    color: var(--charcoal); font-size: 40px;
  }
  .contact {
    position: absolute; left: 56px; top: 130px;
    color: var(--text-grey);
  }
  .contact__name { color: var(--brand-red); font-size: 26px; font-weight: 700; line-height: 1.1; }
  .contact__role { color: var(--charcoal); font-size: 19px; margin-bottom: 18px; }
  .contact__line {
    display: flex; align-items: center; gap: 12px;
    font-size: 19px; line-height: 1.5;
  }
  .contact__line svg { width: 18px; height: 18px; flex: none; }
  .contact__line--plain { padding-left: 0; }

  .card__band {
    position: absolute; left: 0; bottom: 0; width: 700px; height: 70px;
  }
</style>
</head>
<body>
  <main class="sheet">
    <section class="card card--back" aria-label="Card back">
      <div class="wordmark">BRM Constructions</div>
      <div class="website">brmbuild.com</div>
    </section>

    <section class="card card--front" aria-label="Card front">
      <div class="contact">
        <div class="contact__name">Sam Porter</div>
        <div class="contact__role">President</div>
        <div class="contact__line contact__line--plain">ABN: 987654321</div>
        <div class="contact__line">
          <svg viewBox="0 0 24 24" aria-hidden="true"><path fill="#d9121b" d="M6.6 10.8a15.1 15.1 0 0 0 6.6 6.6l2.2-2.2a1 1 0 0 1 1-.25 11.4 11.4 0 0 0 3.6.57 1 1 0 0 1 1 1V20a1 1 0 0 1-1 1A17 17 0 0 1 3 4a1 1 0 0 1 1-1h3.5a1 1 0 0 1 1 1c0 1.25.2 2.45.57 3.6a1 1 0 0 1-.25 1z"/></svg>
          <span>555 0193 4471</span>
        </div>
        <div class="contact__line">
          <svg viewBox="0 0 24 24" aria-hidden="true"><path fill="#d9121b" d="M2 5h20v14H2z"/><path fill="none" stroke="#fff" stroke-width="1.6" d="M2.5 5.5 12 13l9.5-7.5"/></svg>
          <span>sam@brmbuild.com</span>
        </div>
      </div>

      <div class="wordmark">BRM Constructions</div>

      <svg class="card__band" viewBox="0 0 700 70" preserveAspectRatio="none" aria-hidden="true">
        <polygon points="0,54 400,54 392,70 0,70" fill="#d9121b"/>
        <polygon points="408,48 700,48 700,70 396,70" fill="#2b2b2d"/>
      </svg>
    </section>
  </main>
</body>
</html>
```